Business Card Re-Design/Update

We'd like to update out business cards. I've included our current "Style guide" which has the colour scheme of the organisation in it. I've also included the branding files with logos etc in them.

I've also included a copy of one of our existing cards so that you can see how ugly/dated they look. I'd like a fresh modern corporate look.

Target Market(s)

These are for our clients, potential clients, industry contacts - like all business cards

Contact Information for Business Card

Name
Position
Company Address - Level 1, 47 Fernby Street, Carlow Qld 4072
Direct Phone
mobile
Email
Website -www.korvalit.com.au
Logo

Colors

Designer to choose colors to be used in the design.

Requirements
Must have
• Main Logo
• Cards will need to be editable to be able to personalize them for each new employee.
Nice to have
• The MapOut, ShipWell, KeepSteady would be okay to have if they can be sensibly and professionally added to the look without detracting from the main imagery.
• Maybe they could go on the back of the card? will leave this to your creative discretion as to whether/where they fit.
Should not have
• Should not have decorative or script fonts

```html
<!DOCTYPE html>
<html lang="en">
<head>
<meta charset="utf-8">
<title>korvalIT business card</title>
<link rel="stylesheet" href="https://fonts.googleapis.com/css2?family=Arimo:wght@400;700&display=swap">
<style>
  :root {
    --page: #e4e4e4;
    --card: #f7f7f7;
    --brand-red: #b3131b;
    --band-dark: #8e0a10;
    --band-light: #d11820;
    --ink: #1e1e1e;
    --graphic-dark: #262626;
    --muted: #555555;
    --white: #ffffff;
    --plan-green: #5e9b3a;
    --deliver-blue: #1f86c8;
    --sustain-magenta: #b0268f;
  }
  * { margin: 0; padding: 0; box-sizing: border-box; }
  html, body { width: 1200px; height: 960px; overflow: hidden; }
  body {
    background: var(--page);
    font-family: "Arimo", Arial, sans-serif;
    position: relative;
  }
  .card {
    position: absolute;
    width: 600px;
    height: 342px;
    background: var(--card);
    box-shadow: 1px 2px 4px rgba(0,0,0,0.35);
    overflow: hidden;
  }
  .card-front { left: 314px; top: 113px; }
  .card-back { left: 311px; top: 472px; }

  .holder { position: absolute; left: 41px; top: 50px; }
  .holder-name {
    color: var(--brand-red);
    font-size: 21px;
    font-weight: 700;
    letter-spacing: 0.2px;
    line-height: 24px;
  }
  .holder-role { color: var(--ink); font-size: 16.4px; line-height: 19px; }

  .brand {
    position: absolute;
    right: 33px;
    top: 54px;
    display: flex;
    align-items: center;
    gap: 12px;
  }
  .brand-square { width: 30px; height: 30px; background: var(--brand-red); }
  .brand-name { color: var(--ink); font-size: 31px; font-weight: 700; letter-spacing: -0.5px; }

  .band {
    position: absolute;
    left: 0; top: 134px;
    width: 600px; height: 171px;
    background: linear-gradient(120deg, var(--band-light) 0%, #b30f16 45%, var(--band-dark) 100%);
  }
  .band-graphic {
    position: absolute;
    left: 52px; top: 0;
    width: 200px; height: 171px;
    background: linear-gradient(90deg, var(--graphic-dark), #3a3a3a);
  }
  .contact {
    position: absolute;
    right: 30px;
    top: 15px;
    text-align: right;
    color: var(--white);
    font-size: 14px;
    line-height: 18px;
  }
  .contact-address { margin-bottom: 10px; }
  .contact-label { font-weight: 700; }

  .website {
    position: absolute;
    right: 30px;
    bottom: 9px;
    color: var(--muted);
    font-size: 14px;
    letter-spacing: 2.6px;
  }

  .back-brand {
    position: absolute;
    left: 0; top: 100px;
    width: 600px;
    text-align: center;
    color: var(--brand-red);
    font-size: 52px;
    font-weight: 700;
    letter-spacing: -0.5px;
  }
  .services {
    position: absolute;
    left: 0; top: 276px;
    width: 600px;
    display: flex;
    justify-content: center;
    gap: 34px;
  }
  .service { display: flex; align-items: center; gap: 8px; font-size: 25px; font-weight: 700; }
  .service-square { width: 22px; height: 22px; }
  .service-plan { color: var(--plan-green); }
  .service-plan .service-square { background: var(--plan-green); }
  .service-deliver { color: var(--deliver-blue); }
  .service-deliver .service-square { background: var(--deliver-blue); }
  .service-sustain { color: var(--sustain-magenta); }
  .service-sustain .service-square { background: var(--sustain-magenta); }
</style>
</head>
<body>
  <section class="card card-front">
    <div class="holder">
      <p class="holder-name">MAREN HOLT</p>
      <p class="holder-role">Business Development Manager</p>
    </div>
    <div class="brand">
      <span class="brand-square"></span>
      <span class="brand-name">korvalIT</span>
    </div>
    <div class="band">
      <div class="band-graphic" role="img" aria-label="Dark arrow graphic pointing right"></div>
      <div class="contact">
        <p class="contact-address">Level 1, 47 Fernby Street<br>Carlow Qld 4072</p>
        <p><span class="contact-label">P:</span> +61 (0)7 3184 2250</p>
        <p><span class="contact-label">P:</span> +61 (0)7 3184 2257</p>
        <p><span class="contact-label">C:</span> +61 (0)412 506 318</p>
        <p><span class="contact-label">F:</span> +61 (0)7 3184 2299</p>
        <p><span class="contact-label">E:</span> mholt@korvalit.com.au</p>
      </div>
    </div>
    <p class="website">www.korvalit.com.au</p>
  </section>

  <section class="card card-back">
    <p class="back-brand">korvalIT</p>
    <div class="services">
      <span class="service service-plan"><span class="service-square"></span>MapOut</span>
      <span class="service service-deliver"><span class="service-square"></span>ShipWell</span>
      <span class="service service-sustain"><span class="service-square"></span>KeepSteady</span>
    </div>
  </section>
</body>
</html>
```